KR Appraisals website redesign

I would like to refresh my existing website of www.krappraisals-example.com with new graphics, look and feel, as well as updated structure and wording. Content and layout changes have been uploaded to this project Brief.

My existing website has a dark feel. I am now looking for a light and energetic feel. Financial Services is my industry, so the website should be reflect that. I would also like to reflect the concepts of Trust, Service and Expertise.

The website must be serious and upmarket.

Target Market(s)

Corporate board members, CFO's, treasurers and controllers
Auditors, tax advisors, private equity and venture capital asset managers, investors, tax authorities

Industry/Entity Type

Financial Service

Coding

Coded - Design and coding required

Number of Pages Required

5+ page

Font styles to use
Sans Serif
Other font styles liked:
• Designer can choose another modern font

Colors
0355a3
3277b5
85acd3
eaf1f7
f37122
f68d4d
9bcb3c
acd037
cadf82

Requirements
Must have
• Good hi resolution pictures that convey "Finance", "Trust", "Service" or "Expertise".
• An anti-bot (such as Captcha) mechanism in the contact form.
Should not have
• Must not have all content on one rolling screen.

```html
<!DOCTYPE html>
<html lang="en">
<head>
<meta charset="utf-8">
<title>KR Appraisals – Business &amp; Intellectual Property Valuations</title>
<link href="https://fonts.googleapis.com/css2?family=Quicksand:wght@400;500;600;700&family=Raleway:wght@600;700;800&display=swap" rel="stylesheet">
<style>
:root{
  --blue-deep:#0355a3;
  --blue:#3277b5;
  --blue-soft:#85acd3;
  --blue-pale:#eaf1f7;
  --orange:#f37122;
  --orange-soft:#f68d4d;
  --green:#9bcb3c;
  --green-2:#acd037;
  --green-soft:#cadf82;
  --ink:#23364a;
  --muted:#6b7d90;
  --line:#d3e1ee;
  --field:#f3f7fb;
  --white:#ffffff;
}
*{box-sizing:border-box;margin:0;padding:0}
html,body{width:1200px;height:4747px;overflow:hidden;background:var(--white)}
body{font-family:'Quicksand',sans-serif;color:var(--ink);position:relative}
.abs{position:absolute}
.caps{font-family:'Raleway',sans-serif;font-variant:small-caps;font-weight:700;letter-spacing:.5px}

/* top bar */
.topbar{left:0;top:0;width:1200px;height:41px;background:linear-gradient(90deg,var(--blue-deep),var(--blue))}
.topbar .social{left:102px;top:0;height:41px;display:flex;align-items:center;gap:13px;padding:0 14px 0 0}
.topbar .social span{width:10px;height:10px;border-radius:50%;background:var(--white);display:block}
.topbar .social .sep{width:1px;height:41px;background:rgba(255,255,255,.4);margin-left:4px}
.topbar .addr{left:740px;top:0;height:41px;padding-left:10px;border-left:1px solid rgba(255,255,255,.4);display:flex;align-items:center;gap:6px;color:var(--white);font-size:14px;font-weight:500;white-space:nowrap}

/* header */
.header{left:0;top:41px;width:1200px;height:110px;background:var(--white);border-bottom:1px solid var(--line)}
.search{left:160px;top:33px;width:245px;height:44px;border:1px solid var(--line);border-radius:22px;display:flex;align-items:center;padding-left:16px;font-size:14px;color:#8a9bb0}
.search .go{position:absolute;right:4px;top:5px;width:33px;height:33px;border-radius:50%;background:var(--blue-deep)}
.logo{left:480px;top:22px;width:240px;height:72px;display:flex;align-items:center;justify-content:center;gap:10px;font-size:25px;font-weight:600;color:var(--blue-deep);letter-spacing:.5px;white-space:nowrap}
.logo .mark{width:14px;height:14px;background:var(--orange);flex:none}
.call{left:748px;top:32px;display:flex;gap:12px;align-items:center;white-space:nowrap}
.call .txt{font-size:14px;color:var(--muted);line-height:1.6}
.call .txt b{color:var(--ink);font-weight:700;font-size:15px}

/* nav */
.nav{left:0;top:151px;width:1200px;height:65px;background:var(--blue-pale)}
.nav a{position:absolute;top:20px;font-family:'Raleway',sans-serif;font-variant:small-caps;font-size:21px;font-weight:600;color:var(--ink);text-decoration:none;letter-spacing:.6px;white-space:nowrap}
.nav a.active{font-weight:800;color:var(--blue-deep)}
.nav a.active::after{content:"";position:absolute;left:4px;right:4px;bottom:-7px;height:3px;border-radius:2px;background:var(--orange)}

/* hero */
.hero{left:0;top:216px;width:1200px;height:600px;background:linear-gradient(115deg,var(--blue-deep) 0%,var(--blue) 35%,var(--blue-soft) 65%,var(--blue-pale) 85%,var(--blue-soft) 100%)}
.hero h1{left:88px;top:208px;font-size:46px;line-height:64px;color:var(--white);font-weight:800;letter-spacing:1px;text-shadow:0 2px 6px rgba(3,40,80,.35);white-space:nowrap}
.wave{position:absolute;left:0;width:1200px}

/* services */
.section-title{width:1200px;text-align:center;font-size:37px;color:var(--blue-deep)}
.lead{left:130px;width:940px;text-align:center;font-size:15px;line-height:30px;color:var(--muted)}
.service{width:330px;text-align:center}
.service .icon{width:74px;height:74px;margin:0 auto;border-radius:8px;background:linear-gradient(135deg,var(--green-2),var(--green))}
.service h3{margin-top:24px;font-size:16px;color:var(--blue-deep)}
.service p{margin-top:8px;font-size:12px;line-height:25px;color:var(--muted)}

/* trust */
.trust{left:0;top:1474px;width:1200px;height:710px;background:linear-gradient(180deg,var(--blue-deep) 0%,var(--blue) 60%,var(--blue-deep) 100%)}
.trust h2{left:0;top:214px;width:1200px;text-align:center;font-size:40px;color:var(--white);font-weight:800}
.trust p{left:116px;top:280px;width:968px;text-align:justify;text-align-last:center;font-size:16px;line-height:36px;color:var(--white)}
.btn{display:flex;align-items:center;justify-content:center;gap:8px;border-radius:24px;background:linear-gradient(var(--orange-soft),var(--orange));color:var(--white);font-family:'Raleway',sans-serif;font-variant:small-caps;font-weight:700;font-size:17px;letter-spacing:.5px;white-space:nowrap}
.btn .dot{width:15px;height:15px;border-radius:50%;background:var(--white);position:relative}
.btn .dot::after{content:"";position:absolute;left:5px;top:4px;border-left:6px solid var(--orange);border-top:3.5px solid transparent;border-bottom:3.5px solid transparent}

/* blog */
.post{width:330px}
.post .thumb{height:194px;position:relative}
.post .date{position:absolute;left:14px;bottom:-14px;height:30px;padding:0 14px;background:var(--orange);color:var(--white);font-size:14px;display:flex;align-items:center;gap:6px}
.post .date i{width:11px;height:11px;border:2px solid var(--white);display:block}
.post h3{margin-top:36px;font-size:18px;line-height:29px;color:var(--blue-deep);font-weight:700}
.post p{margin-top:14px;font-size:12px;line-height:25px;color:var(--muted)}
.post .more{margin-top:8px;font-size:13px;color:var(--orange)}

/* about */
.about{left:0;top:2820px;width:1200px;height:690px;background:linear-gradient(100deg,var(--blue-deep) 0%,var(--blue) 55%,var(--blue-soft) 100%)}
.about h2{left:88px;top:195px;font-size:39px;color:var(--white);font-weight:800}
.about p{left:88px;top:256px;width:535px;text-align:justify;font-size:14.5px;line-height:31.5px;color:var(--white)}
.about-ring{left:675px;top:2993px;width:412px;height:412px;border-radius:50%;border:4px solid var(--green);border-left-color:var(--white);border-bottom-color:var(--green-soft)}
.about-photo{left:695px;top:3013px;width:372px;height:372px;border-radius:50%;background:radial-gradient(circle at 60% 55%,var(--white) 0%,var(--blue-pale) 35%,var(--blue-soft) 75%,var(--blue) 100%)}

/* contact */
.contact-item{width:300px;text-align:center}
.contact-item .circ{width:84px;height:84px;margin:0 auto;border-radius:50%;background:linear-gradient(var(--blue),var(--blue-deep));display:flex;align-items:center;justify-content:center}
.contact-item p{margin-top:18px;font-size:18px;line-height:28px;color:var(--ink);font-weight:500}
.field{height:39px;background:var(--field);border-bottom:2px solid var(--line);font-size:12px;color:var(--muted);display:flex;align-items:center;padding-left:18px;gap:6px}
.field.area{height:148px;align-items:flex-start;padding-top:12px}
.field i{width:8px;height:8px;border-radius:50%;background:var(--blue);display:block}
.captcha{height:44px;border:1px solid var(--line);background:var(--field);display:flex;align-items:center;gap:10px;padding-left:14px;font-size:13px;color:var(--ink)}
.captcha .box{width:20px;height:20px;border:2px solid var(--blue);background:var(--white);border-radius:3px}

/* footer */
.footer{left:0;top:4257px;width:1200px;height:490px;background:linear-gradient(180deg,var(--blue) 0%,var(--blue-deep) 100%)}
.footer .flogo{left:0;top:170px;width:1200px;text-align:center;font-size:52px;font-weight:500;color:var(--white);letter-spacing:1px}
.footer .fnav{left:0;top:340px;width:1200px;text-align:center;font-size:17px;color:var(--white)}
.footer .fnav span{margin:0 9px;color:var(--green-soft)}
.footer .copy{left:0;top:382px;width:1200px;text-align:center;font-size:15px;color:var(--blue-pale)}
.footer .icons{left:527px;top:423px;display:flex;gap:9px}
.footer .icons span{width:30px;height:30px;border-radius:50%;border:2px solid var(--white);display:block}
</style>
</head>
<body>

<div class="abs topbar">
  <div class="abs social"><span></span><span></span><span></span><span></span><span></span><span></span><span></span><i class="sep"></i></div>
  <div class="abs addr">
    <svg width="11" height="15" viewBox="0 0 11 15"><path d="M5.5 0A5.5 5.5 0 0 0 0 5.5C0 9.5 5.5 15 5.5 15S11 9.5 11 5.5A5.5 5.5 0 0 0 5.5 0Zm0 8A2.5 2.5 0 1 1 5.5 3a2.5 2.5 0 0 1 0 5Z" fill="#fff"/></svg>
    Keizerslaan 48, 2311 AB Leiden, The Netherlands
  </div>
</div>

<header class="abs header">
  <div class="abs search">Search<span class="go"></span></div>
  <div class="abs logo"><span class="mark"></span>KR APPRAISALS</div>
  <div class="abs call">
    <svg width="44" height="44" viewBox="0 0 44 44"><circle cx="22" cy="22" r="20" fill="none" stroke="#0355a3" stroke-width="2.5"/><path d="M15 12c1.5-1 3-1 3.8.4l2 3.4c.6 1-.1 2-.9 2.7l-1 .9c1 2.6 3 4.8 5.6 5.8l.9-1c.8-.8 1.8-1.4 2.8-.8l3.3 2.1c1.3.8 1.3 2.4.3 3.8-1.5 2-3.6 2.6-6 1.6C19.5 29 15.3 24.8 13.6 18.8c-.6-2.5.1-5.2 1.4-6.8Z" fill="#0355a3"/></svg>
    <div class="txt">Call us:<br><b>+31 70 555 0148 &nbsp;/&nbsp; +31 20 555 0172</b></div>
  </div>
</header>

<nav class="abs nav">
  <a class="active" href="index.html" style="left:149px">Home</a>
  <a href="services.html" style="left:280px">Services</a>
  <a href="news.html" style="left:444px">News &amp; Views</a>
  <a href="about.html" style="left:661px">About</a>
  <a href="careers.html" style="left:798px">Careers</a>
  <a href="contact.html" style="left:958px">Contact</a>
</nav>

<section class="abs hero" role="img" aria-label="Photo of business people reviewing financial reports and charts at a desk">
  <h1 class="abs caps">Business &amp; Intellectual<br>Property Valuations</h1>
  <svg class="wave" style="top:480px" width="1200" height="120" viewBox="0 0 1200 120" preserveAspectRatio="none">
    <path d="M0 120V95C300 45 650 22 880 40C1020 52 1130 78 1200 100V120Z" fill="#fff"/>
    <path d="M620 36C800 14 1020 30 1200 92" fill="none" stroke="#f37122" stroke-width="7"/>
  </svg>
</section>

<h2 class="abs section-title caps" style="left:0;top:878px">Our Services</h2>
<p class="abs lead" style="top:940px">Sed ut perspiciatis unde omnis iste natus error sit voluptatem accusantium doloremque laudantium, totam rem aperiam, eaque ipsa quae ab illo inventore veritatis et quasi architecto beatae vitae dicta sunt explicabo.</p>

<div class="abs service" style="left:76px;top:1043px"><div class="icon" role="img" aria-label="Transaction support icon"></div><h3 class="caps">Transaction Support</h3><p>Acquisition, divestment and investment valuations to help you maximize your investment returns.</p></div>
<div class="abs service" style="left:430px;top:1043px"><div class="icon" role="img" aria-label="Financial reporting icon"></div><h3 class="caps">Financial Reporting</h3><p>Purchase price allocations (PPA), goodwill analyses, impairment testing, intangible asset valuations</p></div>
<div class="abs service" style="left:784px;top:1043px"><div class="icon" role="img" aria-label="Fiscal valuations icon"></div><h3 class="caps">Fiscal Valuations</h3><p>Business valuations to support Dutch participation exemption, capital gains and significant interest tests</p></div>
<div class="abs service" style="left:76px;top:1233px"><div class="icon" role="img" aria-label="Finance training icon"></div><h3 class="caps">Finance Training</h3><p>Open-enrollment training to the professional finance and banking markets</p></div>
<div class="abs service" style="left:430px;top:1233px"><div class="icon" role="img" aria-label="Legal support icon"></div><h3 class="caps">Legal Support</h3><p>Business valuations relating to contribution in kind statements "inbrengverklaring" when a company is</p></div>
<div class="abs service" style="left:784px;top:1233px"><div class="icon" role="img" aria-label="Capital advisory icon"></div><h3 class="caps">Capital Advisory</h3><p>Analysis and assessment of strategic options from a valuation and financial perspective</p></div>

<section class="abs trust" role="img" aria-label="Photo of a city skyline with office towers">
  <svg class="wave" style="top:-2px" width="1200" height="90" viewBox="0 0 1200 90" preserveAspectRatio="none">
    <path d="M0 0H1200V12C1000 40 800 70 560 62C350 55 150 28 0 2Z" fill="#fff"/>
  </svg>
  <h2 class="abs caps">Trust, Service &amp; Expertise</h2>
  <p class="abs">Trust is paramount. Clients rely on KR Appraisals for confidentiality, transparency and independence. Service is front and center in KR Appraisals' product offerings. KR Appraisals considers the needs of all stakeholders and the personal needs of the client team involved. KR Appraisals offers more than a decade of valuation experience and maintains its commitment to continual professional development.</p>
  <div class="abs btn" style="left:474px;top:437px;width:252px;height:46px">Download Broucher <span class="dot"></span></div>
  <svg class="wave" style="top:600px" width="1200" height="112" viewBox="0 0 1200 112" preserveAspectRatio="none">
    <path d="M0 112V50C250 20 500 28 700 50C900 72 1080 62 1200 40V112Z" fill="#fff"/>
    <path d="M640 46C850 72 1050 66 1200 38" fill="none" stroke="#9bcb3c" stroke-width="8"/>
  </svg>
</section>

<h2 class="abs section-title caps" style="left:0;top:2255px">Our Blog</h2>

<article class="abs post" style="left:88px;top:2324px">
  <div class="thumb" role="img" aria-label="Illustration of an architectural floor plan with pencils and a magnifier" style="background:linear-gradient(135deg,#eaf1f7,#85acd3 45%,#f4f7fa 70%,#cadf82)"><span class="date"><i></i>Oct 27 2018</span></div>
  <h3 class="caps">Dutch GAAP Update – Goodwill and Definitions of Value</h3>
  <p>Sed ut perspiciatis unde omnis iste natus error sit voluptatem accusantium doloremque laudantium, totam rem aperiam</p>
  <div class="more caps">Read More</div>
</article>
<article class="abs post" style="left:435px;top:2324px">
  <div class="thumb" role="img" aria-label="Photo of glasses, a coffee mug and a property value document" style="background:linear-gradient(135deg,#9bcb3c,#eaf1f7 45%,#ffffff 60%,#f68d4d)"><span class="date"><i></i>Oct 27 2018</span></div>
  <h3 class="caps">Daniel Ross to Speak at Route2Growth on Feb 18 in Oosterhout, the Netherlands</h3>
  <p>Sed ut perspiciatis unde omnis iste natus error sit voluptatem accusantium doloremque laudantium, totam rem aperiam</p>
  <div class="more caps">Read More</div>
</article>
<article class="abs post" style="left:781px;top:2324px">
  <div class="thumb" role="img" aria-label="Illustration of a city skyline on a tablet with a rising chart" style="background:linear-gradient(180deg,#0355a3,#3277b5 55%,#f68d4d 82%,#0355a3)"><span class="date"><i></i>Oct 27 2018</span></div>
  <h3 class="caps">KR Appraisals presenteert bij Route2Growth op 18 februari in Oosterhout</h3>
  <p>Sed ut perspiciatis unde omnis iste natus error sit voluptatem accusantium doloremque laudantium, totam rem aperiam</p>
  <div class="more caps">Read More</div>
</article>

<section class="abs about" role="img" aria-label="Photo of a desk with eyeglasses and paperwork">
  <svg class="wave" style="top:-2px" width="1200" height="80" viewBox="0 0 1200 80" preserveAspectRatio="none">
    <path d="M0 0H1200V20C1000 50 760 70 520 62C320 55 140 30 0 8Z" fill="#fff"/>
  </svg>
  <h2 class="abs caps">About Us</h2>
  <p class="abs">KR Appraisals, founded in 2012, is a boutique valuation advisory practice servicing companies throughout Europe and North America. We have offices in Leiden and Amsterdam. Through our affiliate partners, we also have offices in New York and London offering transfer pricing, derivatives modelling, and machinery &amp; equipment valuation. Our clients come from a broad range of industries with valuations ranging between micro-cap and large-cap.</p>
  <div class="abs btn" style="left:88px;top:455px;width:174px;height:44px">Read More <span class="dot"></span></div>
  <svg class="wave" style="top:600px" width="1200" height="92" viewBox="0 0 1200 92" preserveAspectRatio="none">
    <path d="M0 92V70C200 40 420 30 640 40C860 52 1050 50 1200 26V92Z" fill="#fff"/>
  </svg>
</section>
<div class="abs about-ring"></div>
<div class="abs about-photo" role="img" aria-label="Photo of hands using a calculator over financial documents"></div>

<h2 class="abs section-title caps" style="left:0;top:3597px">Contact Us</h2>
<p class="abs" style="left:0;top:3650px;width:1200px;text-align:center;font-size:18px;color:var(--ink)">Contact us for more information</p>

<div class="abs contact-item" style="left:90px;top:3707px">
  <div class="circ"><svg width="40" height="40" viewBox="0 0 44 44"><path d="M12 8c2-1.3 4-1.3 5 .5l2.7 4.6c.8 1.3-.1 2.7-1.2 3.6l-1.3 1.2c1.4 3.5 4 6.4 7.5 7.8l1.2-1.3c1-1.1 2.4-1.9 3.7-1.1l4.4 2.8c1.7 1.1 1.7 3.2.4 5-2 2.7-4.8 3.5-8 2.1C17.5 30.5 12 25 9.7 17c-.8-3.4.2-7 2.3-9Z" fill="none" stroke="#fff" stroke-width="2"/></svg></div>
  <p>+31 70 555 0148 /<br>+31 20 555 0172</p>
</div>
<div class="abs contact-item" style="left:447px;top:3707px">
  <div class="circ"><svg width="34" height="40" viewBox="0 0 34 40"><path d="M17 2A12 12 0 0 0 5 14c0 9 12 20 12 20s12-11 12-20A12 12 0 0 0 17 2Z" fill="none" stroke="#fff" stroke-width="2"/><circle cx="17" cy="14" r="4.5" fill="none" stroke="#fff" stroke-width="2"/><path d="M3 38h28" stroke="#fff" stroke-width="2"/></svg></div>
  <p>Keizerslaan 48, 2311 AB Leiden<br>The Netherlands</p>
</div>
<div class="abs contact-item" style="left:784px;top:3707px">
  <div class="circ"><svg width="36" height="36" viewBox="0 0 36 36"><rect x="4" y="12" width="28" height="20" rx="2" fill="#fff"/><rect x="10" y="4" width="16" height="10" fill="#fff"/><g fill="#0355a3"><rect x="18" y="17" width="3" height="3"/><rect x="23" y="17" width="3" height="3"/><rect x="18" y="22" width="3" height="3"/><rect x="23" y="22" width="3" height="3"/><rect x="8" y="16" width="6" height="12"/></g></svg></div>
  <p>Email:<br>info@krappraisals-example.com</p>
</div>

<form class="abs" style="left:160px;top:3897px;width:878px;height:280px">
  <div class="abs field" style="left:0;top:0;width:430px"><i></i>First Name</div>
  <div class="abs field" style="left:450px;top:0;width:428px"><i></i>Last Name</div>
  <div class="abs field" style="left:0;top:54px;width:430px"><i></i>Company</div>
  <div class="abs field area" style="left:450px;top:54px;width:428px"><i></i>How can i help you? :</div>
  <div class="abs field" style="left:0;top:108px;width:430px"><i></i>Email Address</div>
  <div class="abs field" style="left:0;top:163px;width:430px"><i></i>Phone Number</div>
  <div class="abs captcha" style="left:0;top:228px;width:240px"><span class="box"></span>I am not a robot</div>
  <div class="abs btn" style="left:352px;top:228px;width:174px;height:44px">Submit <span class="dot"></span></div>
</form>

<footer class="abs footer" role="img" aria-label="Photo of a canal street with historic brick houses">
  <svg class="wave" style="top:-2px" width="1200" height="80" viewBox="0 0 1200 80" preserveAspectRatio="none">
    <path d="M0 0H1200V50C1000 30 820 32 600 46C380 60 180 52 0 20Z" fill="#fff"/>
    <path d="M0 24C180 56 380 62 600 48" fill="none" stroke="#f37122" stroke-width="7"/>
  </svg>
  <div class="abs flogo">KR APPRAISALS</div>
  <div class="abs fnav caps">Home<span>|</span>Our Services<span>|</span>News &amp; Views<span>|</span>About Us<span>|</span>Careers<span>|</span>Contact Us</div>
  <div class="abs copy caps">© 2019 Company Name. All right reserved</div>
  <div class="abs icons"><span></span><span></span><span></span><span></span></div>
</footer>

</body>
</html>
```